Investment Management Firm Power point template

Marrow Holdings is a real estate investment firm focused on buying commercial office and residential property in the UK. We produce powerpoint presentations for our Board of Directors, Investment Committee and also to external investors.

We are looking for a powerpoint design template which we can use for future presentations which provide a professional look and feel.

Our current website: http://www.marrowholdings.example.co.uk/

Target Market(s)

Institution Investors, Board of Directors, Professionals

Industry/Entity Type

Real Estate

Requirements
Must have
• Leverage off the current logo and colour scheme. However, does not have to purely rely on this colour scheme.
• - Title page
• - Content Page
• - Slide where graphs can be incorporated
• - Slide where photos can be incorporated
• - Slide of UK Map which can show where the property portfolio is currently located
• - Other slides incorporating smart art or other designs that can be used for future presentations
Nice to have
• An example of graphics that we would love to have in the powerpoint pack which we can easily edit has been attached

```html
<!DOCTYPE html>
<html lang="en">
<head>
<meta charset="utf-8">
<title>Marrow Holdings – Presentation Template</title>
<link href="https://fonts.googleapis.com/css2?family=Catamaran:wght@400;600;700&family=Open+Sans:ital,wght@0,400;0,600;0,700;1,400&display=swap" rel="stylesheet">
<style>
:root{
  --stage:#000;
  --navy:#1e4f7c;
  --blue:#2b6596;
  --deep:#173d63;
  --teal:#2d8fb1;
  --sky:#41aadb;
  --charcoal:#2f2f2f;
  --grey:#6b6b6b;
  --mist:#d9d9d9;
  --paper:#ffffff;
  --text:#5a5a5a;
}
*{margin:0;padding:0;box-sizing:border-box}
html,body{width:959px;height:1200px;overflow:hidden;background:var(--stage)}
.board{position:relative;width:959px;height:1200px;font-family:"Open Sans",sans-serif}
.slide{position:absolute;width:309px;height:231px;overflow:hidden;background:var(--paper)}
.slide.dark{background:var(--blue);color:#fff}
.title{position:absolute;left:9px;top:8px;font:700 9.5px/1 "Catamaran",sans-serif;color:var(--navy);border-bottom:1px solid var(--navy);padding-bottom:1px}
.footer{position:absolute;left:0;right:0;bottom:0;height:11px;background:var(--blue)}
.copyright{position:absolute;left:5px;bottom:3px;font-size:3.6px;color:#fff}
.brand-tag{position:absolute;right:5px;bottom:1px;background:#fff;padding:2px 4px 1px;display:flex;align-items:center;gap:2px;font:700 5.6px/1 "Catamaran",sans-serif;color:var(--navy)}
.brand-tag i{display:block;width:4px;height:4px;background:var(--navy)}
.body{position:absolute;font-size:3.7px;line-height:1.55;color:var(--text)}
.body p{margin-bottom:4px}
.body b{color:var(--navy)}
.body em{color:var(--blue);font-weight:700}
.sub{font:700 5.6px/1.2 "Catamaran",sans-serif;color:var(--navy);margin-bottom:3px}
.media{position:absolute}
.photo-city{background:linear-gradient(160deg,#3d72a3,#23527e 60%,#1b4268)}
.photo-room{background:linear-gradient(135deg,#e4e2dc,#cfcac0 45%,#9aa9a6 80%,#6e7b79)}
.photo-tower{background:linear-gradient(150deg,#c8dbe9,#7ea4c6 50%,#3f6891)}
.photo-person{background:linear-gradient(180deg,#e3e3e3,#a5a5a5)}
.placeholder{position:absolute;background:#d6d6d6;color:#f2f2f2;font-size:4px;display:flex;align-items:center;justify-content:center}
.center{text-align:center}
</style>
</head>
<body>
<div class="board">

<!-- 1 Cover -->
<section class="slide dark" style="left:8px;top:6px;">
  <div class="media photo-city" role="img" aria-label="City skyline at dusk tinted in blue" style="inset:0;"></div>
  <div style="position:absolute;left:72px;top:101px;width:165px;height:32px;border:1px solid rgba(255,255,255,.8);display:flex;align-items:center;justify-content:center;font:600 15px/1 'Catamaran',sans-serif;color:#fff;">Marrow Holdings</div>
  <p class="center" style="position:absolute;left:40px;right:40px;top:147px;font:700 6.6px/1.45 'Open Sans',sans-serif;">Marrow Holdings is the new property arm<br>of the Harwick Stone Group</p>
</section>

<!-- 2 About Us -->
<section class="slide dark" style="left:325px;top:6px;">
  <div class="media photo-city" role="img" aria-label="Glass office tower in blue tint" style="left:142px;top:0;right:0;bottom:0;opacity:.75;"></div>
  <h2 style="position:absolute;left:12px;top:9px;font:700 9.5px/1 'Catamaran',sans-serif;">About Us</h2>
  <div class="center" style="position:absolute;left:25px;top:62px;width:260px;height:107px;border:1px solid rgba(255,255,255,.35);padding:12px 10px;font-size:3.7px;line-height:1.6;color:#e8f0f7;">
    <p style="margin-bottom:6px">While a property's fundamentals matter to us, we put equal focus on the people who use and enjoy our spaces. The experience of being in our buildings — from design to atmosphere — is carefully planned. Function and efficiency are central to our approach.</p>
    <p style="margin-bottom:6px">With these core characteristics in mind we aim to create businesses around our properties, enhancing their value and building long-term operating platforms.</p>
    <p>As part of the Harwick Stone Group we directly and indirectly benefit from the ecosystem of companies around us. Harwick Stone brings unrivalled expertise in building successful, long-lasting businesses.</p>
  </div>
  <div class="brand-tag" style="left:4px;right:auto;bottom:3px;">Marrow Holdings</div>
</section>

<!-- 3 Image band -->
<section class="slide" style="left:643px;top:6px;">
  <div class="title">Slide Title Here</div>
  <div class="media photo-city" role="img" aria-label="River and city skyline in blue tint" style="left:0;right:0;top:24px;height:128px;"></div>
  <div class="body" style="left:19px;top:49px;width:275px;color:#e9f1f8;">
    <p class="sub" style="color:#fff">Lorem ipsum dolor sit amet</p>
    <p>Placeholder copy describing the property portfolio and how each asset supports our long-term plans for growth. <b style="color:#fff">Key message in bold here.</b></p>
    <p>Further supporting copy that outlines strategy, location and the value we create for tenants and investors.</p>
    <p style="margin-top:10px">Additional summary line for the board, noting timing and next steps for approval.</p>
  </div>
  <div class="body" style="left:19px;top:163px;width:275px;">
    <p>Placeholder copy describing the property portfolio and how each asset supports our long-term plans. <b>Key message in bold here.</b></p>
    <p>Further supporting copy that outlines strategy, location and the value we create for investors.</p>
  </div>
  <div class="footer"><span class="copyright">Copyright text here</span></div>
</section>

<!-- 4 Pie chart -->
<section class="slide" style="left:8px;top:246px;">
  <div class="title">Slide Title Here</div>
  <div class="body" style="left:20px;top:47px;width:140px;">
    <p class="sub">Subtitle Here</p>
    <p>Placeholder copy describing the chart and the main finding it shows for the period under review. <b>Key figure noted here.</b></p>
    <p>Supporting copy that explains the split between sectors and how it compares with the previous year.</p>
    <p>Further notes on allocation, income and risk across the portfolio, with comments on targets for the next period of activity.</p>
  </div>
  <svg style="position:absolute;left:176px;top:58px;" width="124" height="124" viewBox="-62 -62 124 124" aria-label="Pie chart">
    <path d="M0 0 L0 -52 A52 52 0 0 1 30.6 -42.1Z" fill="var(--sky)"/>
    <path d="M0 0 L30.6 -42.1 A52 52 0 0 1 27.9 43.9Z" fill="var(--navy)"/>
    <path d="M0 0 L27.9 43.9 A52 52 0 0 1 -50.4 12.9Z" fill="var(--charcoal)"/>
    <path d="M0 0 L-50.4 12.9 A52 52 0 0 1 0 -52Z" fill="var(--teal)"/>
    <g fill="#fff" font-family="Catamaran,sans-serif" font-weight="700" font-size="10">
      <text x="5" y="-33">10%</text><text x="22" y="9">31%</text>
      <text x="-18" y="33">30%</text><text x="-40" y="-5">29%</text>
    </g>
  </svg>
  <div class="footer"><span class="copyright">Copyright text here</span><span class="brand-tag"><i></i>Marrow Holdings</span></div>
</section>

<!-- 5 Location -->
<section class="slide" style="left:325px;top:246px;">
  <div class="title">Our Location</div>
  <div class="media" role="img" aria-label="Dotted map of the UK and Ireland with property pins" style="left:52px;top:30px;width:148px;height:180px;background:radial-gradient(ellipse at 60% 55%,#c9c9c9,#e4e4e4 60%,#fff 75%);"></div>
  <div class="body" style="left:204px;top:44px;width:100px;">
    <p class="sub" style="font-size:5px;color:var(--blue)">Our Property Location Portfolio</p>
    <p style="margin:0">•&nbsp; Property Portfolio Name Here<br>•&nbsp; Property Portfolio Name Here<br>•&nbsp; Property Portfolio Name Here<br>•&nbsp; Property Portfolio Name Here<br>•&nbsp; Property Portfolio Name Here</p>
  </div>
  <div class="body" style="left:243px;top:194px;display:flex;align-items:center;gap:3px;"><span style="width:7px;height:7px;border-radius:50%;background:var(--blue);border:1.5px solid #cfe0ee;"></span>Property Portfolio</div>
  <div class="footer"><span class="brand-tag"><i></i>Marrow Holdings</span></div>
</section>

<!-- 6 Two columns -->
<section class="slide" style="left:643px;top:246px;">
  <div class="title">Slide Title Here</div>
  <div class="body" style="left:18px;top:45px;width:120px;">
    <p class="sub" style="color:var(--blue)">Content Paragraph Title</p>
    <p>While a property's fundamentals matter to us, we put equal focus on the people who use and enjoy our spaces. The experience of being in our buildings — from design to atmosphere — is carefully planned.</p>
    <p>With these core characteristics in mind we aim to create businesses around our properties, enhancing value and building long-term platforms.</p>
    <p>As part of the Harwick Stone Group we benefit from the ecosystem of companies around us, with unrivalled expertise in building lasting businesses.</p>
  </div>
  <div class="body" style="left:168px;top:45px;width:120px;">
    <p class="sub" style="color:var(--blue)">Content Paragraph Title</p>
    <p>While a property's fundamentals matter to us, we put equal focus on the people who use and enjoy our spaces. The experience of being in our buildings — from design to atmosphere — is carefully planned.</p>
    <p>With these core characteristics in mind we aim to create businesses around our properties, enhancing value and building long-term platforms.</p>
    <p>As part of the Harwick Stone Group we benefit from the ecosystem of companies around us, with unrivalled expertise in building lasting businesses.</p>
  </div>
  <div class="footer"><span class="brand-tag"><i></i>Marrow Holdings</span></div>
</section>

<!-- 7 Text + image placeholders -->
<section class="slide" style="left:8px;top:486px;">
  <div class="title">Slide Title Here</div>
  <div class="body" style="left:17px;top:42px;width:125px;">
    <p class="sub" style="color:var(--blue)">Content Paragraph Title</p>
    <p>While a property's fundamentals matter to us, we put equal focus on the people who use and enjoy our spaces. The experience of being in our buildings — from design to atmosphere — is carefully planned. Function and efficiency are central.</p>
    <p>With these core characteristics in mind we aim to create businesses around our properties, enhancing value and building long-term platforms.</p>
    <p>As part of the Harwick Stone Group we directly and indirectly benefit from the ecosystem of companies around us, with expertise in building lasting businesses.</p>
  </div>
  <div class="placeholder" style="left:175px;top:44px;width:117px;height:72px;">Image Here</div>
  <div class="placeholder" style="left:175px;top:126px;width:117px;height:72px;">Image Here</div>
  <div class="footer"><span class="brand-tag"><i></i>Marrow Holdings</span></div>
</section>

<!-- 8 Team -->
<section class="slide" style="left:325px;top:486px;">
  <div class="title" style="top:10px;font-size:8.5px">Team Title Here</div>
  <div class="media photo-person" role="img" aria-label="Team member portrait" style="left:9px;top:35px;width:90px;height:90px;"></div>
  <div class="media photo-person" role="img" aria-label="Team member portrait" style="left:109px;top:35px;width:90px;height:90px;"></div>
  <div class="media photo-person" role="img" aria-label="Team member portrait" style="left:209px;top:35px;width:90px;height:90px;"></div>
  <div class="body" style="left:11px;top:134px;width:290px;">
    <p>Placeholder biography copy introducing the team and the experience each member brings to the investment process. <b>Key role noted here.</b></p>
    <p>Supporting copy covering background, sector focus and the markets in which the team has delivered results.</p>
    <p style="margin-top:8px">Closing line on governance and how the team reports to the board and committee.</p>
  </div>
  <div class="footer"><span class="copyright">Copyright text here</span></div>
</section>

<!-- 9 Section -->
<section class="slide dark" style="left:643px;top:486px;">
  <h2 class="center" style="position:absolute;left:0;right:0;top:96px;font:700 15.5px/1 'Catamaran',sans-serif;">Section Slide Title</h2>
  <p class="center" style="position:absolute;left:40px;right:40px;top:124px;font:italic 4.2px/1.6 'Open Sans',sans-serif;color:#dce8f2;">While a property's fundamentals matter to us, we put equal focus on the people who use<br>and enjoy our spaces. The experience of being in our buildings</p>
  <span class="brand-tag"><i></i>Marrow Holdings</span>
</section>

<!-- 10 Circles -->
<section class="slide" style="left:8px;top:725px;">
  <div class="title">Slide Title Here</div>
  <div class="body" style="left:19px;top:47px;width:125px;">
    <p>While a property's fundamentals matter to us, we put equal focus on the people who use and enjoy our spaces. The experience of being in our buildings — from design to atmosphere — is carefully planned.</p>
    <p><em><i>With these core characteristics in mind we aim to create businesses around our properties</i></em></p>
    <p>As part of the Harwick Stone Group we directly and indirectly benefit from the ecosystem of companies around us, with expertise in building lasting businesses.</p>
  </div>
  <svg style="position:absolute;left:164px;top:50px;" width="130" height="130" viewBox="0 0 130 130" aria-label="Percentage circles">
    <circle cx="36" cy="37" r="30" fill="var(--charcoal)"/>
    <circle cx="94" cy="37" r="30" fill="#5c5c5c"/>
    <circle cx="36" cy="95" r="30" fill="var(--teal)"/>
    <circle cx="94" cy="95" r="30" fill="var(--deep)"/>
    <g fill="none" stroke="#fff" stroke-width="1.6" opacity=".9">
      <circle cx="36" cy="37" r="30"/><circle cx="94" cy="37" r="30"/><circle cx="36" cy="95" r="30"/><circle cx="94" cy="95" r="30"/>
    </g>
    <g fill="#fff" font-family="Catamaran,sans-serif">
      <text x="17" y="44" font-size="19">70<tspan font-size="9">%</tspan></text>
      <text x="75" y="102" font-size="19">30<tspan font-size="9">%</tspan></text>
      <g font-size="3.8" text-anchor="middle" font-family="Open Sans,sans-serif">
        <text x="94" y="31">Short label text</text><text x="94" y="36">for this value</text><text x="94" y="41">goes here</text>
        <text x="36" y="89">Short label text</text><text x="36" y="94">for this value</text><text x="36" y="99">goes here</text>
      </g>
    </g>
  </svg>
  <div class="footer"><span class="brand-tag"><i></i>Marrow Holdings</span></div>
</section>

<!-- 11 Arc chart -->
<section class="slide" style="left:325px;top:725px;">
  <div class="title" style="font-size:8.5px">Slide Title Here</div>
  <div class="body" style="left:20px;top:45px;width:135px;">
    <p class="sub">Subtitle Here</p>
    <p>Placeholder copy describing the chart and the main finding it shows for the period. <b>Key figure noted here.</b></p>
    <p>Supporting copy explaining the split between sectors and how it compares with the prior year.</p>
    <p>Further notes on allocation, income and risk across the portfolio, with comments on targets for the next period of activity and reporting.</p>
  </div>
  <svg style="position:absolute;left:170px;top:46px;" width="130" height="130" viewBox="-65 -65 130 130" aria-label="Concentric arc chart">
    <g fill="none" transform="rotate(-40)">
      <circle r="55" stroke="var(--teal)" stroke-width="7" stroke-dasharray="260 346"/>
      <circle r="45" stroke="var(--charcoal)" stroke-width="7" stroke-dasharray="90 283"/>
      <circle r="45" stroke="var(--navy)" stroke-width="7" stroke-dasharray="0 95 120 283"/>
      <circle r="35" stroke="#6b6b6b" stroke-width="6" stroke-dasharray="0 60 110 220"/>
      <circle r="35" stroke="var(--sky)" stroke-width="6" stroke-dasharray="55 220"/>
      <circle r="26" stroke="var(--blue)" stroke-width="5" stroke-dasharray="0 40 85 163"/>
    </g>
    <rect x="-9" y="-9" width="18" height="18" fill="var(--navy)"/>
  </svg>
  <div class="footer"><span class="copyright">Copyright text here</span></div>
</section>

<!-- 12 Thanks -->
<section class="slide" style="left:643px;top:725px;">
  <div style="position:absolute;left:70px;top:69px;display:flex;align-items:center;gap:5px;font:700 19px/1 'Catamaran',sans-serif;color:var(--charcoal);"><span style="display:block;width:14px;height:14px;background:var(--navy)"></span>Marrow Holdings</div>
  <div style="position:absolute;left:0;right:0;top:108px;bottom:0;background:var(--blue);border-top:2px solid #d6e2ec;"></div>
  <h2 class="center" style="position:absolute;left:0;right:0;top:126px;font:700 12.5px/1 'Catamaran',sans-serif;color:#fff;">Thanks for your Time</h2>
  <p class="center" style="position:absolute;left:0;right:0;top:155px;font:italic 5.4px/1.7 'Open Sans',sans-serif;color:#e3ecf4;">12 Alder Row,<br>London EC9 1ZZ<br>+44 (0) 200 000 0147<br>info@marrowholdings.example.co.uk</p>
</section>

<!-- 13 Services -->
<section class="slide" style="left:8px;top:965px;">
  <div class="title">Slide Title Here</div>
  <svg style="position:absolute;left:0;top:48px;" width="309" height="60" viewBox="0 0 309 60" aria-label="Service icons">
    <g fill="none" stroke="var(--blue)">
      <circle cx="60" cy="30" r="28" stroke="#cfd8e0" stroke-width="1"/><circle cx="60" cy="30" r="24" stroke-width="1.5"/>
      <circle cx="155" cy="30" r="28" stroke="#cfd8e0" stroke-width="1"/><circle cx="155" cy="30" r="24" stroke-width="1.5"/>
      <circle cx="250" cy="30" r="28" stroke="#cfd8e0" stroke-width="1"/><circle cx="250" cy="30" r="24" stroke-width="1.5"/>
      <g stroke-width="2">
        <rect x="48" y="20" width="24" height="16"/><path d="M56 41h8M60 36v5"/>
        <rect x="147" y="17" width="16" height="26" rx="2"/>
        <rect x="238" y="20" width="24" height="16"/><path d="M246 41h8M250 36v5"/>
      </g>
    </g>
  </svg>
  <div class="body center" style="left:12px;top:118px;width:95px;"><p class="sub" style="color:var(--blue);font-weight:600">Service Title Here</p><p>While a property's fundamentals matter to us, we put equal focus on the people who use and enjoy our spaces. The experience of being in our buildings.</p></div>
  <div class="body center" style="left:107px;top:118px;width:95px;"><p class="sub" style="color:var(--blue);font-weight:600">Service Title Here</p><p>While a property's fundamentals matter to us, we put equal focus on the people who use and enjoy our spaces. The experience of being in our buildings.</p></div>
  <div class="body center" style="left:202px;top:118px;width:95px;"><p class="sub" style="color:var(--blue);font-weight:600">Service Title Here</p><p>While a property's fundamentals matter to us, we put equal focus on the people who use and enjoy our spaces. The experience of being in our buildings.</p></div>
  <div class="footer"><span class="brand-tag"><i></i>Marrow Holdings</span></div>
</section>

<!-- 14 Text + photo -->
<section class="slide" style="left:325px;top:965px;">
  <div class="title">Slide Title Here</div>
  <div class="body" style="left:17px;top:43px;width:125px;">
    <p class="sub" style="font-size:5px">Subtext Heading Here</p>
    <p>While a property's fundamentals matter to us, we put equal focus on the people who use and enjoy our spaces. The experience of being in our buildings — from design to atmosphere — is carefully planned. Function and efficiency are central.</p>
    <p><em><i>With these core characteristics in mind we aim to create businesses around our properties</i></em></p>
    <p>As part of the Harwick Stone Group we directly and indirectly benefit from the ecosystem of companies around us, with expertise in building lasting businesses.</p>
  </div>
  <div class="media photo-room" role="img" aria-label="Bright loft apartment interior with kitchen and large windows" style="left:154px;top:0;right:0;bottom:11px;"></div>
  <div class="footer"><span class="brand-tag"><i></i>Marrow Holdings</span></div>
</section>

<!-- 15 Two photos -->
<section class="slide" style="left:643px;top:965px;">
  <div class="title">Slide Title Here</div>
  <div class="media photo-tower" role="img" aria-label="Glass office towers viewed from below" style="left:0;top:31px;width:148px;height:183px;"></div>
  <div class="media photo-room" role="img" aria-label="Loft apartment interior with kitchen" style="left:155px;top:31px;width:154px;height:183px;"></div>
  <div class="center" style="position:absolute;left:0;top:187px;width:148px;height:27px;background:rgba(43,101,150,.82);color:#fff;font-size:3.7px;line-height:1.5;padding:5px 8px;">While a property's fundamentals matter to us, we put equal focus on the people who use and enjoy our spaces. The experience of being in our buildings</div>
  <div class="center" style="position:absolute;left:155px;top:187px;width:154px;height:27px;background:rgba(43,101,150,.82);color:#fff;font-size:3.7px;line-height:1.5;padding:5px 8px;">While a property's fundamentals matter to us, we put equal focus on the people who use and enjoy our spaces. The experience of being in our buildings</div>
  <div class="footer" style="background:#fff;border-top:3px solid var(--blue);height:14px;"><span class="brand-tag" style="bottom:2px"><i></i>Marrow Holdings</span></div>
</section>

</div>
</body>
</html>
```